Business Card Design

Carl Brenton Insurance Agency, an Independent Insurance Agency which was stated on Pine Street in Laplace, Louisiana on 1958 and has grown the six locations throughout South Louisiana. We sell personal (auto Homeowners flood, liability) and commercial insurance (commercial property, general liability, workers compensation, commercial auto). I am looking for a double sided card with list the five remaining locations on the back or maybe even a folded four sided card. Our home office is a two story building with a green roof. I have had a logo designed which I have attached. Open for revisions but would like to stay with in the same green roof over an M. I have attached the logo but can not tell if I was uploaded.

Target Market(s)

Individual and commercial insurance buyers. Upper income and business owners

Industry/Entity Type

Insurance

Requirements
Must have
• Must have similar logo as uploaded. Green roof over M or something similar. List all location address and phone numbers.

Employee name, office phone number; direct phone line; email address and website list all locations on card. Very Similar colors to current logo.
Nice to have
• Possible folded card with double sided print

```html
<!DOCTYPE html>
<html lang="en">
<head>
<meta charset="utf-8">
<title>Carl Brenton Insurance Agency – Business Card</title>
<link href="https://fonts.googleapis.com/css2?family=Titillium+Web:wght@400;700&display=swap" rel="stylesheet">
<style>
  :root{
    --page:#e9eaec;
    --card:#ffffff;
    --green:#255040;
    --green-dark:#1e4436;
    --blue:#1f5fa8;
    --ink-light:#ffffff;
    --shadow:rgba(0,0,0,.18);
  }
  *{box-sizing:border-box;margin:0;padding:0}
  html,body{width:1200px;height:900px;overflow:hidden}
  body{
    background:var(--page);
    font-family:"Titillium Web",Arial,sans-serif;
    display:flex;align-items:center;justify-content:center;gap:40px;
  }
  .card{
    position:relative;width:540px;height:310px;
    background:var(--card);border-radius:34px;overflow:hidden;
    box-shadow:0 10px 30px var(--shadow);
  }
  .card-shape{position:absolute;inset:0;width:100%;height:100%}
  .contact-panel{
    position:absolute;left:30px;top:30px;width:200px;color:var(--ink-light);
  }
  .person-name{font-size:17px;font-weight:400;letter-spacing:.06em;text-transform:uppercase;line-height:1.1}
  .person-role{font-size:13px;opacity:.9;margin-bottom:18px}
  .office-address{font-size:12.5px;line-height:1.35;margin:0 0 20px 40px}
  .contact-list{list-style:none;font-size:12.5px;line-height:1.55}
  .contact-list li{display:flex;align-items:center;gap:7px}
  .contact-list svg{width:11px;height:11px;flex:none;fill:var(--ink-light)}
  .brand{
    position:absolute;display:flex;flex-direction:column;
  }
  .brand-front{left:268px;top:132px}
  .brand-back{left:50%;top:50%;transform:translate(-50%,-50%);align-items:flex-start}
  .brand-row{display:flex;align-items:center;gap:8px}
  .brand-mark{width:18px;height:18px;background:var(--green);flex:none}
  .brand-name{
    color:var(--green);font-weight:700;font-size:17px;line-height:1.05;
    text-transform:uppercase;letter-spacing:.02em;
  }
  .brand-back .brand-name{font-size:24px}
  .brand-back .brand-mark{width:24px;height:24px}
  .brand-tagline{color:var(--blue);font-size:11.5px;font-weight:700;margin:3px 0 0 26px}
  .brand-back .brand-tagline{font-size:14px;margin-left:32px}
</style>
</head>
<body>

  <section class="card card-front">
    <svg class="card-shape" viewBox="0 0 540 310" aria-hidden="true">
      <path d="M0 0 H250 Q205 150 178 310 H0 Z" fill="var(--green)"/>
      <path d="M262 0 Q217 150 190 310" fill="none" stroke="var(--blue)" stroke-width="6"/>
    </svg>
    <div class="contact-panel">
      <p class="person-name">Martin Delacroix</p>
      <p class="person-role">Managing Director</p>
      <p class="office-address">214 Cedar Lane, Suite 3<br>Laplace LA</p>
      <ul class="contact-list">
        <li><svg viewBox="0 0 12 12"><path d="M3 0h6v12H3z M4 1v9h4V1z"/></svg>985 555 0142</li>
        <li><svg viewBox="0 0 12 12"><rect x="1" y="3" width="10" height="8"/><rect x="3" y="0" width="6" height="3"/></svg>985 555 0143</li>
        <li><svg viewBox="0 0 12 12"><path d="M0 2h12v8H0z M1 3l5 4 5-4z" fill-rule="evenodd"/></svg>985 555 0144</li>
        <li><svg viewBox="0 0 12 12"><circle cx="6" cy="6" r="5.5"/></svg>martin@brentonagency.com</li>
        <li><svg viewBox="0 0 12 12"><path d="M6 .5a5.5 5.5 0 1 0 0 11a5.5 5.5 0 1 0 0-11zm0 1.5v8M2 6h8" stroke="#fff" fill="none"/></svg>www.brentonagency.com</li>
      </ul>
    </div>
    <div class="brand brand-front">
      <div class="brand-row">
        <span class="brand-mark"></span>
        <p class="brand-name">Carl Brenton<br>Insurance Agency</p>
      </div>
      <p class="brand-tagline">Serving Pine Street Since 1958</p>
    </div>
  </section>

  <section class="card card-back">
    <div class="brand brand-back">
      <div class="brand-row">
        <span class="brand-mark"></span>
        <p class="brand-name">Carl Brenton<br>Insurance Agency</p>
      </div>
      <p class="brand-tagline">Serving Pine Street Since 1958</p>
    </div>
  </section>

</body>
</html>
```